Website for Torvel Capital - investment banking firm

We have a corporate identity (thanks to Ravinka/31842) and want to extend that into a website design.  See the attached zipped files.
We have software folks in-house to do the coding.
See the attached Project Brief & Notes for more details.  Don't worry about the actual text - lorem ipsum will be fine.
The server will be Apache.
Thank you!
Desmond

Industry/Entity Type
Investment

```html
<!DOCTYPE html>
<html lang="en">
<head>
<meta charset="utf-8">
<title>Torvel Capital — Investment Banking</title>
<link rel="stylesheet" href="https://fonts.googleapis.com/css2?family=Open+Sans:wght@400;600&family=Raleway:wght@500;600&display=swap">
<style>
:root{
  --topbar:#7d7b8b;
  --navy:#1f4d8f;
  --navy-dark:#163a6e;
  --btn:#3a77d0;
  --text:#333333;
  --muted:#555555;
  --link:#2f6bbf;
  --panel:#e1e1e1;
  --rule:#dddddd;
  --footer:#7d7b8b;
  --footer-dark:#5c5a68;
  --white:#ffffff;
}
*{box-sizing:border-box;margin:0;padding:0}
html,body{width:1026px;height:1200px;overflow:hidden}
body{font-family:"Open Sans",sans-serif;color:var(--text);background:var(--white);position:relative}
ul{list-style:none}
a{color:inherit;text-decoration:none}

.topbar{height:35px;background:var(--topbar);color:var(--white);font-size:11px}
.topbar .wrap{width:838px;margin:0 auto;height:35px;display:flex;align-items:center;justify-content:space-between}
.topbar .group{display:flex;align-items:center;gap:12px}
.topbar .sep{opacity:.8}

.header{width:838px;margin:0 auto;height:91px;display:flex;align-items:center;justify-content:space-between}
.brand{display:flex;align-items:center;gap:10px}
.brand-mark{width:38px;height:38px;background:var(--navy)}
.brand-name{font-size:26px;font-weight:600;color:var(--navy);letter-spacing:.5px}
.search{display:flex;width:235px;height:31px}
.search-field{flex:1;border:1px solid #ccc;border-right:0;background:#f2f2f2;font-size:11px;color:#999;padding:0 9px;display:flex;align-items:center}
.search-btn{width:47px;background:var(--navy);color:var(--white);font-size:17px;display:flex;align-items:center;justify-content:center}

.nav{width:838px;margin:0 auto;height:34px;background:var(--navy);border-radius:3px;display:flex;padding-left:15px}
.nav a{color:var(--white);font-size:12px;padding:0 15px;display:flex;align-items:center;text-transform:uppercase}
.nav a.active{background:var(--navy-dark)}

.hero{width:838px;height:343px;margin:14px auto 0;position:relative;background:linear-gradient(100deg,#c9d0da 0%,#bfc3c5 35%,#a88a4a 60%,#c9a350 78%,#b5c2d4 100%)}
.hero-copy{position:absolute;left:29px;top:74px}
.hero h1{font-family:"Raleway",sans-serif;font-weight:500;font-size:26px;line-height:30px;color:#1d2a3e}
.hero p{font-family:"Raleway",sans-serif;font-weight:500;font-size:14px;line-height:19px;color:#111;margin-top:10px}
.hero .btn{display:inline-flex;align-items:center;justify-content:center;width:162px;height:39px;background:var(--btn);color:var(--white);font-family:"Raleway",sans-serif;font-weight:600;font-size:16px;margin-top:18px}

.features{width:838px;height:168px;margin:31px auto 0;background:var(--panel);display:flex;gap:22px;padding:21px 17px}
.feature{width:253px;height:123px;position:relative}
.feature-img{position:absolute;inset:0}
.feature-label{position:absolute;left:0;right:0;bottom:0;height:37px;background:rgba(20,20,20,.85);color:var(--white);font-family:"Raleway",sans-serif;font-size:18px;display:flex;align-items:center;justify-content:center}

.deals{width:838px;margin:38px auto 0;display:flex}
.deal{flex:1;padding:0 0 0 2px;height:162px}
.deal + .deal{border-left:1px solid var(--rule);padding-left:34px}
.deal h2{font-weight:400;font-size:18px;color:#222;margin-bottom:12px}
.deal li{font-size:11px;color:var(--muted);line-height:24px;padding-left:13px;position:relative}
.deal li::before{content:"›";position:absolute;left:0;color:var(--link)}
.deal li.more{color:var(--link);line-height:14px;padding-left:15px}

.footer{position:absolute;left:0;top:940px;width:1026px;height:223px;background:var(--footer);color:var(--white)}
.footer .col{position:absolute;top:20px}
.footer h3{font-weight:400;font-size:16px;margin-bottom:18px}
.footer li{font-size:10.5px;line-height:17px}
.footer .bullets li{padding-left:13px;position:relative}
.footer .bullets li::before{content:"";position:absolute;left:1px;top:7px;width:3px;height:3px;border-radius:50%;background:var(--white)}
.contact li{display:flex;gap:6px;align-items:center}
.contact svg{width:11px;height:11px;flex:none}
.map{width:263px;height:110px;border:2px solid var(--white);border-radius:3px;background:linear-gradient(135deg,#e9e2c8,#d9d6b8 50%,#b9d0e6)}
.copyright{position:absolute;left:0;top:1163px;width:1026px;height:37px;background:var(--footer-dark);color:var(--white);font-size:11px;display:flex;align-items:center;justify-content:center}
</style>
</head>
<body>

<div class="topbar">
  <div class="wrap">
    <div class="group">
      <svg width="30" height="16" viewBox="0 0 30 16" aria-hidden="true"><circle cx="8" cy="8" r="7" fill="none" stroke="#fff" stroke-width="1.5"/><path d="M1 8h14M8 1v14" stroke="#fff" stroke-width="1"/><path d="M22 7l3 3 3-3z" fill="#fff"/></svg>
      <span>Asia</span><span class="sep">|</span><span>Contact us</span>
    </div>
    <div class="group">
      <svg width="12" height="12" viewBox="0 0 12 12" aria-hidden="true"><path d="M2 1h3l1 3-2 1a7 7 0 0 0 3 3l1-2 3 1v3c-5 0-9-4-9-9z" fill="#fff"/></svg>
      <span>0800.418.236</span><span class="sep">|</span><span>Login</span>
      <svg width="13" height="13" viewBox="0 0 13 13" aria-hidden="true"><path d="M7 1h5v11H7" fill="none" stroke="#fff" stroke-width="1.5"/><path d="M1 6.5h7M5 3.5l3 3-3 3" fill="none" stroke="#fff" stroke-width="1.5"/></svg>
    </div>
  </div>
</div>

<header class="header">
  <div class="brand"><span class="brand-mark"></span><span class="brand-name">Torvel Capital</span></div>
  <div class="search"><div class="search-field">Search..</div><div class="search-btn">GO</div></div>
</header>

<nav class="nav">
  <a class="active" href="#">Home</a><a href="#">About</a><a href="#">Services</a><a href="#">Current Engagements</a><a href="#">Completed Transactions</a>
</nav>

<section class="hero">
  <div role="img" aria-label="Stacks of gold coins on financial papers" style="position:absolute;inset:0"></div>
  <div class="hero-copy">
    <h1>Torvel Capital, LLC Investment<br>Banking Mergers &amp;Acquisitions</h1>
    <p>Sed ut perspiciatis unde omnis iste natus error sit totam<br>Duis aute irure dolor in reprehenderit in voluptate velit.</p>
    <a class="btn" href="#">Read More</a>
  </div>
</section>

<section class="features">
  <div class="feature"><div class="feature-img" role="img" aria-label="Businessman stacking coins" style="background:linear-gradient(135deg,#1f232c,#4a4f5a 55%,#b89658)"></div><div class="feature-label">Who we are</div></div>
  <div class="feature"><div class="feature-img" role="img" aria-label="Hand holding a payment card at a laptop" style="background:linear-gradient(135deg,#2c3d5e,#7f93b8 55%,#c9d6ea)"></div><div class="feature-label">What we do</div></div>
  <div class="feature"><div class="feature-img" role="img" aria-label="Globe on banknotes" style="background:linear-gradient(135deg,#dfe6f0,#9fb3cf 55%,#4f6b99)"></div><div class="feature-label">Our services</div></div>
</section>

<section class="deals">
  <div class="deal">
    <h2>Buy-SideAcquisitions</h2>
    <ul><li>Lorem ipsum dolor sit amet, consectetur</li><li>adipisicing elit, sed do eiusmod tempor</li><li>incididunt ut labore et dolore magna aliqua.</li><li>Ut enim ad minim veniam</li><li class="more">Veiw all</li></ul>
  </div>
  <div class="deal">
    <h2>Recapitalizations</h2>
    <ul><li>Lorem ipsum dolor sit amet, consectetur</li><li>adipisicing elit, sed do eiusmod tempor</li><li>incididunt ut labore et dolore magna aliqua.</li><li>Ut enim ad minim veniam</li><li class="more">Veiw all</li></ul>
  </div>
  <div class="deal">
    <h2>Sell-SideTransactions</h2>
    <ul><li>Lorem ipsum dolor sit amet, consectetur</li><li>adipisicing elit, sed do eiusmod tempor</li><li>incididunt ut labore et dolore magna aliqua.</li><li>Ut enim ad minim veniam</li><li class="more">Veiw all</li></ul>
  </div>
</section>

<footer class="footer">
  <div class="col" style="left:94px">
    <h3>Site Linke</h3>
    <ul class="bullets"><li>Home</li><li>About</li><li>Services</li><li>Current Engagements</li><li>Completed Transactions</li></ul>
  </div>
  <div class="col" style="left:288px;top:18px">
    <h3>Resources</h3>
    <ul class="bullets"><li>Blog</li><li>Articles</li><li>Webinars</li><li>Events</li><li>Downloads</li></ul>
  </div>
  <div class="col contact" style="left:438px">
    <h3>Contact us</h3>
    <ul>
      <li><svg viewBox="0 0 11 11" aria-hidden="true"><path d="M5.5 1L1 5h1.5v5h2.5V7h1v3h2.5V5H10z" fill="#fff"/></svg>Request A Free Demo</li>
      <li style="padding-left:17px">Contact</li>
      <li><svg viewBox="0 0 11 11" aria-hidden="true"><rect x="3" y="0.5" width="5" height="10" rx="1" fill="none" stroke="#fff"/></svg>Phone: 866-404-7312</li>
      <li><svg viewBox="0 0 11 11" aria-hidden="true"><rect x="1" y="3" width="9" height="7" fill="#fff"/><rect x="3" y="0.5" width="5" height="3" fill="none" stroke="#fff"/></svg>Fax: 866-404-7319</li>
    </ul>
  </div>
  <div class="col" style="left:628px">
    <h3>Our Location</h3>
    <div class="map" role="img" aria-label="Regional map with office location pins"></div>
  </div>
</footer>
<div class="copyright">© Copyright 2014. All rights reseverd.</div>

</body>
</html>
```